Website for Swedish wellness company "Heartmeadow"

We need a website for our Swedish wellness company. The name is "Heartmeadow" . The company is all about sustainablility for our body, soul and planet. We work with coaching, yoga, massage, healthy food, retreats(sports, excercise, sufing), healing and inspirational talks. We are convinced that personal sustainability and a strong spiritual connection to yourself will lead to planetary sustainability. Our customers are both companies and consumers from all over the world. The final design should be clean/simple and you should get a feeling of community, happiness, warmth, connection,, joy, spirituality but still a professional touch.Just got a logo from Pixel Harbor and are very happy with it;-)
Updates

Sorry I was too enthusiastic posting this project. Of course I will give you some text as well för the different pages! I will see to that it is finished by friday so if you want to wait with your submissions please do! Best regards Maria

Target Market(s)

Businesses and consumers

Industry/Entity Type

Health And Wellness

Number of Pages Required

5+ page

Font styles to use
Sans Serif

Colors
33a6d7
00a990
b7a5cd

Requirements
Must have
• Idea about pages:
• I am not sure how many pages I get for the price, but 5 would be nice to start with.
• Not sure what write ups is;-)
• But title of the pages could be:
• Landing page
• About us
• Services
• Retreats
• Contact us
Nice to have
• A clean and professional website but with some heart and soul in it. Because we Would love colours that harmonize with our logo, but other ideas are welcome!

```html
<!DOCTYPE html>
<html lang="en">
<head>
<meta charset="utf-8">
<title>Heartmeadow – Wellness for body, soul and planet</title>
<link href="https://fonts.googleapis.com/css2?family=Lato:wght@400;700;900&display=swap" rel="stylesheet">
<style>
:root{
  --blue:#33a6d7;
  --blue-deep:#2b8fc4;
  --green:#00a990;
  --purple:#b7a5cd;
  --purple-deep:#9d8cc0;
  --ink:#2e2e33;
  --text:#5b5d63;
  --muted:#9a9ca3;
  --line:#d8dbe0;
  --white:#ffffff;
}
*{box-sizing:border-box;margin:0;padding:0}
html,body{width:1200px;height:3760px;overflow:hidden}
body{font-family:"Lato",Arial,sans-serif;color:var(--text);background:var(--white);position:relative}
.btn{display:inline-block;font-size:13px;font-weight:700;letter-spacing:1px;text-transform:uppercase;color:var(--white);padding:14px 28px;border-radius:3px}
.btn-green{background:var(--green)}
.btn-purple{background:var(--purple-deep)}
.photo{position:absolute}

/* header */
.site-header{position:absolute;top:0;left:0;width:1200px;height:124px;background:var(--white);border-top:6px solid var(--purple)}
.brand{position:absolute;left:70px;top:22px;display:flex;align-items:center;gap:14px}
.brand-dot{width:54px;height:54px;border-radius:50%;background:var(--blue)}
.brand-name{font-size:30px;font-weight:900;color:var(--ink);letter-spacing:1px}
.topbar{position:absolute;right:70px;top:22px;display:flex;align-items:center;gap:22px}
.phone{display:flex;align-items:center;gap:8px;color:var(--blue);font-size:17px;font-weight:700}
.main-nav{position:absolute;right:70px;top:86px;display:flex;gap:30px;font-size:13px;font-weight:700;letter-spacing:1px}
.main-nav a{color:var(--ink)}
.main-nav a.active{color:var(--green)}

/* hero */
.hero{position:absolute;top:124px;left:0;width:1200px;height:700px;overflow:hidden}
.hero .photo{inset:0;background:linear-gradient(100deg,#6f7478 0%,#a9aaa6 45%,#d6d2c8 75%,#b8b1a4 100%)}
.hero-content{position:absolute;left:70px;top:210px;color:var(--white)}
.hero-title{font-size:56px;font-weight:900;letter-spacing:2px}
.hero-sub{font-size:26px;font-weight:700;line-height:1.35;margin:12px 0 36px;width:520px}
.hero-dots{position:absolute;left:70px;top:470px;display:flex;gap:10px}
.hero-dots span{width:12px;height:12px;border-radius:50%;background:var(--white);opacity:.6}
.hero-dots span:first-child{opacity:1}
.hero-wave{position:absolute;left:0;bottom:0}

/* welcome */
.welcome{position:absolute;top:810px;left:0;width:1200px;height:420px}
.welcome-text{position:absolute;left:70px;top:0;width:620px}
h2{font-size:30px;font-weight:900;color:var(--ink);letter-spacing:1px;text-transform:uppercase}
.welcome p{font-size:15px;line-height:1.7;margin-top:18px}
.welcome .btn{margin-top:28px}
.welcome .photo{left:760px;top:-20px;width:400px;height:400px;border-radius:50%;border:10px solid var(--white);box-shadow:0 4px 18px rgba(0,0,0,.18);background:radial-gradient(circle at 50% 55%,#f4b36a 0%,#d77a55 35%,#6d5a8a 70%,#2e3f6e 100%)}

/* services */
.services{position:absolute;top:1180px;left:0;width:1200px;height:560px}
.services-bg{position:absolute;inset:0}
.services h2{position:absolute;top:140px;width:100%;text-align:center;color:var(--white)}
.service-cards{position:absolute;left:70px;top:208px;display:flex;gap:24px}
.service-card{width:246px;height:222px;background:rgba(255,255,255,.25);border-radius:4px;text-align:center;padding-top:30px;color:var(--white)}
.service-card:first-child{background:rgba(183,165,205,.55)}
.service-card svg{display:block;margin:0 auto}
.service-card h3{font-size:16px;font-weight:900;letter-spacing:1px;margin:16px 0 10px}
.service-card p{font-size:13px;line-height:1.5;padding:0 26px}
.slider-dots{position:absolute;top:468px;left:570px;display:flex;gap:8px}
.slider-dots span{width:24px;height:6px;border-radius:3px;background:var(--white);opacity:.5}
.slider-dots span:first-child{opacity:1}

/* testimonials */
.testimonials{position:absolute;top:1800px;left:0;width:1200px;height:560px;text-align:center}
.testimonial-row{display:flex;gap:28px;margin:40px 70px 0}
.testimonial{width:352px}
.testimonial .photo{position:relative;height:208px;border-radius:3px}
.play{position:absolute;left:50%;top:50%;transform:translate(-50%,-50%)}
.testimonial blockquote{font-size:14px;line-height:1.6;margin:18px 14px 14px}
.testimonial h4{font-size:20px;font-weight:700;color:var(--blue)}
.testimonials .btn{margin-top:38px}

/* retreats */
.retreats{position:absolute;top:2360px;left:0;width:1200px;height:580px}
.retreats .photo{left:70px;top:88px;width:380px;height:380px;border-radius:50%;border:10px solid var(--white);box-shadow:0 4px 18px rgba(0,0,0,.18);background:linear-gradient(160deg,#8fb7c9 0%,#c6a68a 45%,#6b7f66 100%)}
.retreats-text{position:absolute;left:500px;top:150px;width:600px;color:var(--white)}
.retreats-text h2{color:var(--white)}
.retreats-text p{font-size:15px;line-height:1.7;margin:16px 0 28px}

/* appointment */
.appointment{position:absolute;top:2990px;left:0;width:1200px;text-align:center}
.appt-form{width:604px;margin:40px auto 0;display:grid;grid-template-columns:1fr 1fr;gap:18px 24px;text-align:left}
.field{height:44px;border:1px solid var(--line);border-radius:2px;font-size:13px;color:var(--muted);padding:13px 14px;position:relative}
.field.wide{grid-column:1/3;height:96px}
.field .caret{position:absolute;right:14px;top:14px}
.appointment .btn{margin-top:26px;padding:14px 76px}

/* footer */
.site-footer{position:absolute;top:3380px;left:0;width:1200px;height:380px;color:var(--white)}
.footer-bg{position:absolute;inset:0}
.footer-brand{position:absolute;left:70px;top:130px;width:250px}
.footer-logo{display:flex;flex-direction:column;align-items:flex-start;gap:10px}
.footer-logo .brand-dot{width:44px;height:44px;background:var(--white);opacity:.85}
.footer-logo .brand-name{color:var(--white);font-size:24px}
.footer-brand small{display:block;font-size:12px;margin-top:16px;line-height:1.6}
.footer-col{position:absolute;top:130px}
.footer-col h5{font-size:16px;font-weight:900;letter-spacing:1px;margin-bottom:14px}
.footer-col li{list-style:none;font-size:13px;line-height:2.15}
.col-map{left:370px}
.col-services{left:585px}
.col-contact{left:905px}
.col-contact li{display:flex;align-items:center;gap:8px}
.socials{display:flex;gap:12px;margin-top:12px}
.socials span{width:22px;height:22px;border-radius:50%;background:var(--white)}
.to-top{position:absolute;right:30px;bottom:24px;font-size:11px}
</style>
</head>
<body>

<header class="site-header">
  <div class="brand"><span class="brand-dot"></span><span class="brand-name">HEARTMEADOW</span></div>
  <div class="topbar">
    <span class="phone">
      <svg width="18" height="18" viewBox="0 0 24 24"><path fill="#33a6d7" d="M6.6 10.8a15.1 15.1 0 0 0 6.6 6.6l2.2-2.2a1 1 0 0 1 1-.25 11.4 11.4 0 0 0 3.6.57 1 1 0 0 1 1 1V20a1 1 0 0 1-1 1A17 17 0 0 1 3 4a1 1 0 0 1 1-1h3.5a1 1 0 0 1 1 1c0 1.25.2 2.45.57 3.57a1 1 0 0 1-.25 1z"/></svg>
      1-800-555-0142
    </span>
    <span class="btn btn-green">Book an appointment</span>
  </div>
  <nav class="main-nav">
    <a class="active">HOME</a><a>ABOUT</a><a>SERVICES</a><a>RETREATS</a><a>CONTACT US</a>
  </nav>
</header>

<section class="hero">
  <div class="photo" role="img" aria-label="Group of people meditating in a bright yoga studio"></div>
  <div class="hero-content">
    <h1 class="hero-title">HEARTMEADOW</h1>
    <p class="hero-sub">Maecenas elit massa, commodo commodo fermentum convallis.</p>
    <span class="btn btn-purple">Contact us today</span>
  </div>
  <div class="hero-dots"><span></span><span></span><span></span></div>
  <svg class="hero-wave" width="1200" height="120" viewBox="0 0 1200 120" preserveAspectRatio="none">
    <path d="M0 70 C250 10 450 120 700 80 S1050 20 1200 60 L1200 120 L0 120Z" fill="#ffffff"/>
  </svg>
</section>

<section class="welcome">
  <div class="welcome-text">
    <h2>Welcome to our website</h2>
    <p>We believe that caring for your body and soul is the first step towards caring for our planet. Through coaching, yoga, massage and healthy food we help people find balance, calm and a strong connection to themselves and to each other.</p>
    <p>Our team welcomes companies and private guests from all over the world. Join a session, book a retreat or simply come and meet our warm community in the heart of Sweden.</p>
    <span class="btn btn-green">Read more</span>
  </div>
  <div class="photo" role="img" aria-label="Person meditating on a beach at sunset"></div>
</section>

<section class="services">
  <svg class="services-bg" width="1200" height="560" viewBox="0 0 1200 560" preserveAspectRatio="none">
    <defs>
      <linearGradient id="svcGrad" x1="0" y1="0" x2="1" y2="0">
        <stop offset="0" stop-color="#b7a5cd"/><stop offset=".45" stop-color="#33a6d7"/><stop offset="1" stop-color="#2b8fc4"/>
      </linearGradient>
    </defs>
    <path d="M0 80 C300 20 600 120 900 60 S1150 40 1200 60 L1200 500 C900 560 600 470 300 520 S50 520 0 510Z" fill="url(#svcGrad)"/>
  </svg>
  <h2>Services</h2>
  <div class="service-cards">
    <div class="service-card">
      <svg width="56" height="56" viewBox="0 0 56 56"><circle cx="20" cy="14" r="7" fill="#fff"/><circle cx="38" cy="18" r="6" fill="#fff"/><path d="M8 46c0-12 6-20 12-20s12 8 12 20Z M30 46c0-10 4-16 8-16s10 6 10 16Z" fill="#fff"/></svg>
      <h3>COACHING</h3><p>Personal guidance towards a calmer and kinder everyday life.</p>
    </div>
    <div class="service-card">
      <svg width="56" height="56" viewBox="0 0 56 56"><circle cx="28" cy="10" r="6" fill="#fff"/><path d="M28 18v16M14 26l14 6 14-6M10 46c6-6 12-8 18-8s12 2 18 8" stroke="#fff" stroke-width="4" fill="none" stroke-linecap="round"/></svg>
      <h3>YOGA</h3><p>Gentle classes for every level to move, breathe and rest.</p>
    </div>
    <div class="service-card">
      <svg width="56" height="56" viewBox="0 0 56 56"><circle cx="14" cy="26" r="6" fill="#fff"/><rect x="20" y="24" width="30" height="8" rx="4" fill="#fff"/><rect x="6" y="36" width="46" height="4" fill="#fff"/><path d="M12 40v8M46 40v8" stroke="#fff" stroke-width="4"/></svg>
      <h3>MASSAGE</h3><p>Relaxing treatments that release tension and restore energy.</p>
    </div>
    <div class="service-card">
      <svg width="56" height="56" viewBox="0 0 56 56"><path d="M28 48C12 36 6 28 6 19a11 11 0 0 1 22-3 11 11 0 0 1 22 3c0 9-6 17-22 29Z" fill="#fff"/><path d="M28 38V24c0-5 4-8 8-8" stroke="#33a6d7" stroke-width="3" fill="none"/></svg>
      <h3>HEALTHY FOOD</h3><p>Fresh, local and seasonal meals that nourish body and planet.</p>
    </div>
  </div>
  <div class="slider-dots"><span></span><span></span></div>
</section>

<section class="testimonials">
  <h2>Customer testimonials</h2>
  <div class="testimonial-row">
    <article class="testimonial">
      <div class="photo" role="img" aria-label="Video thumbnail of a smiling older woman" style="background:linear-gradient(135deg,#b9c2c8,#e7ddd2)">
        <svg class="play" width="44" height="44" viewBox="0 0 44 44"><circle cx="22" cy="22" r="22" fill="#fff" opacity=".9"/><path d="M18 14l12 8-12 8Z" fill="#33a6d7"/></svg>
      </div>
      <blockquote>“A truly warm place. The retreat gave me new energy and a calmer mind that I still carry with me today.”</blockquote>
      <h4>Name Heading</h4>
    </article>
    <article class="testimonial">
      <div class="photo" role="img" aria-label="Video thumbnail of a smiling woman with red hair" style="background:linear-gradient(135deg,#7d6a5c,#d9b08e)">
        <svg class="play" width="44" height="44" viewBox="0 0 44 44"><circle cx="22" cy="22" r="22" fill="#fff" opacity=".9"/><path d="M18 14l12 8-12 8Z" fill="#33a6d7"/></svg>
      </div>
      <blockquote>“The coaching sessions helped our whole team slow down and connect. We will surely come back next year.”</blockquote>
      <h4>Name Heading</h4>
    </article>
    <article class="testimonial">
      <div class="photo" role="img" aria-label="Video thumbnail of a smiling older couple" style="background:linear-gradient(135deg,#3f4a57,#a79582)">
        <svg class="play" width="44" height="44" viewBox="0 0 44 44"><circle cx="22" cy="22" r="22" fill="#fff" opacity=".9"/><path d="M18 14l12 8-12 8Z" fill="#33a6d7"/></svg>
      </div>
      <blockquote>“Wonderful food, lovely people and yoga every morning. A week we will remember for a very long time.”</blockquote>
      <h4>Name Heading</h4>
    </article>
  </div>
  <span class="btn btn-green">View all testimonials</span>
</section>

<section class="retreats">
  <svg class="services-bg" width="1200" height="580" viewBox="0 0 1200 580" preserveAspectRatio="none" style="position:absolute;inset:0">
    <defs>
      <linearGradient id="retGrad" x1="0" y1="0" x2="1" y2="0">
        <stop offset="0" stop-color="#b7a5cd"/><stop offset=".55" stop-color="#6fa6d8"/><stop offset="1" stop-color="#33a6d7"/>
      </linearGradient>
    </defs>
    <path d="M0 40 C300 110 700 0 1200 70 L1200 520 C900 470 500 590 0 530Z" fill="url(#retGrad)"/>
  </svg>
  <div class="photo" role="img" aria-label="Smiling woman leading an outdoor group exercise class"></div>
  <div class="retreats-text">
    <h2>Retreats</h2>
    <p>Join us for a week of sport, exercise, surfing and stillness by the sea. Our retreats combine movement, healing and inspiring talks with good food and a caring community that feels like home.</p>
    <span class="btn btn-green">Read more</span>
  </div>
</section>

<section class="appointment">
  <h2>Request an appointment</h2>
  <form class="appt-form">
    <div class="field">Name</div>
    <div class="field">Email Address</div>
    <div class="field">City</div>
    <div class="field">Subject
      <svg class="caret" width="10" height="14" viewBox="0 0 10 14"><path d="M1 5l4-4 4 4M1 9l4 4 4-4" stroke="#9a9ca3" fill="none"/></svg>
    </div>
    <div class="field wide">Message</div>
  </form>
  <span class="btn btn-green">Submit now</span>
</section>

<footer class="site-footer">
  <svg class="footer-bg" width="1200" height="380" viewBox="0 0 1200 380" preserveAspectRatio="none">
    <defs>
      <linearGradient id="footGrad" x1="0" y1="0" x2="1" y2="0">
        <stop offset="0" stop-color="#33a6d7"/><stop offset="1" stop-color="#2b8fc4"/>
      </linearGradient>
    </defs>
    <path d="M0 60 C300 0 700 110 1200 40 L1200 380 L0 380Z" fill="url(#footGrad)"/>
  </svg>
  <div class="footer-brand">
    <div class="footer-logo"><span class="brand-dot"></span><span class="brand-name">HEARTMEADOW</span></div>
    <small>Copyright © 2017 · Heartmeadow<br>All Rights Reserved</small>
  </div>
  <div class="footer-col col-map">
    <h5>SITE MAP</h5>
    <ul><li>Home</li><li>About Us</li><li>Services</li><li>Retreats</li><li>Contact Us</li></ul>
  </div>
  <div class="footer-col col-services">
    <h5>SERVICES</h5>
    <ul><li>Coaching</li><li>Yoga</li><li>Massage</li><li>Healthy Food</li><li>Retreats Healing &amp; Inspirational Talks</li></ul>
  </div>
  <div class="footer-col col-contact">
    <h5>CONTACT INFO</h5>
    <ul>
      <li><svg width="12" height="14" viewBox="0 0 12 16"><path d="M6 0a6 6 0 0 1 6 6c0 4-6 10-6 10S0 10 0 6a6 6 0 0 1 6-6Z" fill="#fff"/><circle cx="6" cy="6" r="2" fill="#33a6d7"/></svg>Meadow Lane 12, Lund</li>
      <li style="padding-left:20px">Sweden</li>
      <li><svg width="12" height="12" viewBox="0 0 24 24"><path fill="#fff" d="M6.6 10.8a15.1 15.1 0 0 0 6.6 6.6l2.2-2.2a1 1 0 0 1 1-.25 11.4 11.4 0 0 0 3.6.57 1 1 0 0 1 1 1V20a1 1 0 0 1-1 1A17 17 0 0 1 3 4a1 1 0 0 1 1-1h3.5a1 1 0 0 1 1 1c0 1.25.2 2.450.57 3.57a1 1 0 0 1-.25 1z"/></svg>1-800-555-0142</li>
      <li><svg width="12" height="10" viewBox="0 0 16 12"><rect width="16" height="12" rx="1" fill="#fff"/><path d="M0 1l8 6 8-6" stroke="#33a6d7" fill="none"/></svg>hello@heartmeadow.se</li>
    </ul>
    <div class="socials"><span></span><span></span><span></span><span></span><span></span></div>
  </div>
  <span class="to-top">TOP</span>
</footer>

</body>
</html>
```